Fresh, modern, fun business card for pediatric dental practice

Need a business card for fresh, modern, fun pediatric dental practice

Clean look that matches our website's font and colors

We prefer the look of curved corners on business cards

Target Market(s)

parents (mothers) of young children, professionals, mid-high class

Industry/Entity Type

Dental

Contact Information for Business Card

Maplebrook Pediatric Dentistry
482 Quarry Lane
Suite 517
Alder Falls, PA 17058
717.555.0193
www.maplebrookkidsdental.example

Mei-Ran Tsai, DMD
Corinne Walbeck, DMD
(we are working on our email address, but we would like that on the card as well)

Font styles to use
Sans Serif

Requirements
Must have
• All info; we would also like to make cards for individual staff members
• colors from our website and color palatte, attatched
• use same font and design as website for branding
Nice to have
• clean, simple card that has a pop of color
• we would like to see a few designs with our tag line "where smiles get brighter"
• we are not sure if we want to have it on there or not
• we would like to see a few designs incorporating the ribbon graphic on our website where the word WELCOME is

```html
<!DOCTYPE html>
<html lang="en">
<head>
<meta charset="utf-8">
<title>Maplebrook Pediatric Dentistry – Business Card</title>
<link rel="stylesheet" href="https://fonts.googleapis.com/css2?family=Roboto:wght@400;500;700&family=Lato:wght@400&display=swap">
<style>
  :root {
    --plum: #4e2548;
    --sun: #f0b323;
    --berry: #c92a8f;
    --ink: #ffffff;
    --stage: #d6d6d6;
  }
  * { box-sizing: border-box; margin: 0; padding: 0; }
  html, body { width: 1200px; height: 1134px; overflow: hidden; }
  body { background: var(--stage); position: relative; font-family: "Lato", sans-serif; }

  .card {
    position: absolute;
    left: 261px;
    width: 675px;
    height: 381px;
    background: var(--plum);
    border-radius: 14px;
    overflow: hidden;
  }
  .card--front { top: 161px; }
  .card--back { top: 590px; }

  .practice-name {
    position: absolute;
    font-family: "Roboto", sans-serif;
    font-weight: 700;
    color: var(--sun);
    text-align: center;
    line-height: 1.15;
  }
  .practice-name__dot {
    display: block;
    width: 34px; height: 34px;
    margin: 0 auto 12px;
    border-radius: 50%;
    background: var(--sun);
  }
  .card--front .practice-name { left: 30px; top: 110px; width: 280px; font-size: 27px; }
  .card--back .practice-name { left: 0; top: 118px; width: 100%; font-size: 38px; }

  .divider {
    position: absolute;
    left: 331px; top: 76px;
    width: 2px; height: 202px;
    background: var(--sun);
  }

  .details { position: absolute; left: 366px; top: 70px; color: var(--ink); }
  .dentists { font-family: "Roboto", sans-serif; font-weight: 700; font-size: 25px; line-height: 36px; }
  .dentists .title { color: var(--sun); font-weight: 400; }
  .address { margin-top: 14px; font-size: 15px; line-height: 21px; }
  .contacts { list-style: none; margin-top: 15px; font-size: 15px; }
  .contacts li { display: flex; align-items: center; height: 24px; }
  .contacts svg { width: 18px; height: 18px; margin-right: 9px; flex: none; }

  .welcome-ribbon { position: absolute; left: 173px; top: 313px; width: 317px; height: 44px; }
  .welcome-ribbon span {
    position: absolute; inset: 0;
    display: flex; align-items: center; justify-content: center;
    font-family: "Roboto", sans-serif; font-weight: 700; font-size: 27px; color: var(--ink);
  }
</style>
</head>
<body>

<section class="card card--front" aria-label="Business card front">
  <div class="practice-name">
    <span class="practice-name__dot"></span>
    Maplebrook<br>Pediatric Dentistry
  </div>

  <div class="divider"></div>

  <div class="details">
    <p class="dentists">Mei-Ran Tsai, <span class="title">DMD</span></p>
    <p class="dentists">Corinne Walbeck, <span class="title">DMD</span></p>
    <p class="address">482 Quarry Lane, Suite 517<br>Alder Falls, PA 17058</p>
    <ul class="contacts">
      <li>
        <svg viewBox="0 0 18 18" aria-hidden="true"><circle cx="9" cy="9" r="9" fill="#f0b323"/><path d="M6 4.5l1.8 0 .8 2.3-1.2.9a6 6 0 0 0 2.9 2.9l.9-1.2 2.3.8v1.8c0 .6-.5 1-1.1 1A8 8 0 0 1 5 5.6c0-.6.4-1.1 1-1.1z" fill="#4e2548"/></svg>
        717.555.0193
      </li>
      <li>
        <svg viewBox="0 0 18 18" aria-hidden="true"><circle cx="9" cy="9" r="9" fill="#f0b323"/><rect x="4.5" y="6" width="9" height="6.5" rx="1" fill="#4e2548"/><path d="M4.8 6.4L9 9.6l4.2-3.2" fill="none" stroke="#f0b323" stroke-width="1"/></svg>
        info@maplebrookkidsdental.example
      </li>
      <li>
        <svg viewBox="0 0 18 18" aria-hidden="true"><circle cx="9" cy="9" r="9" fill="#f0b323"/><circle cx="9" cy="9" r="4.6" fill="none" stroke="#4e2548" stroke-width="1.3"/><path d="M4.4 9h9.2M9 4.4c-2 2.6-2 6.6 0 9.2M9 4.4c2 2.6 2 6.6 0 9.2" fill="none" stroke="#4e2548" stroke-width="1"/></svg>
        www.maplebrookkidsdental.example
      </li>
    </ul>
  </div>

  <div class="welcome-ribbon">
    <svg viewBox="0 0 317 44" width="317" height="44" aria-hidden="true"><polygon points="0,0 317,0 304,22 317,44 0,44 13,22" fill="#c92a8f"/></svg>
    <span>welcome</span>
  </div>
</section>

<section class="card card--back" aria-label="Business card back">
  <div class="practice-name">
    <span class="practice-name__dot"></span>
    Maplebrook<br>Pediatric Dentistry
  </div>
</section>

</body>
</html>
```